WordPress webdesign with coding for our company BRISK The Answer

BRISK The Answer is a payrolling company such as Montaval Wages (one of our competitor https://www.montaval-wages.ch/fr/). We need to set up our website in both languages (Fr and Eng). Our logo is enclosed.
we would like something simple explaining what is payrolling in Graph and wording, who we are and a contact page. you can also take some example if needed from our mother company BRISK The Horizon (www.briskthehorizon.ch) or our sister company (www.briskyourstride.ch). we would like to keep the color panel of our logo (ref. Black = PANTONE P Process Black C
Pink = PANTONE P Process Magenta C
Grey = PANTONE 430 C) as the driver of the website.

```html
<!DOCTYPE html>
<html lang="en">
<head>
<meta charset="utf-8">
<title>BRISK The Answer – Payrolling</title>
<link href="https://fonts.googleapis.com/css2?family=Fira+Sans:ital,wght@0,300;0,400;0,500;0,600;0,700;1,400&display=swap" rel="stylesheet">
<style>
:root{
  --pink:#e6007e;
  --black:#1a1a1a;
  --grey:#7c878e;
  --text:#555b60;
  --light:#f1eff0;
  --footer:#3d3d3d;
  --white:#fff;
}
*{box-sizing:border-box;margin:0;padding:0}
html,body{width:1200px;height:3624px;overflow:hidden}
body{font-family:"Fira Sans",Arial,sans-serif;color:var(--black);background:var(--white);position:relative}
.pink{color:var(--pink)}
.abs{position:absolute}
.btn{display:inline-block;background:var(--pink);color:#fff;font-weight:600;font-size:16px;padding:11px 16px;border-radius:4px;text-decoration:none}
.btn.dark{background:#3a3a3a}

/* header */
.site-header{position:absolute;left:0;top:0;width:1200px;height:78px;background:#fff;display:flex;align-items:center}
.brand{position:absolute;left:111px;top:20px;display:flex;align-items:center;gap:10px;font-size:26px;font-weight:700;color:var(--black)}
.brand-mark{width:16px;height:16px;background:var(--pink)}
.main-nav{position:absolute;left:377px;top:30px;display:flex;gap:32px;font-size:16px;color:#333}
.main-nav .active{color:var(--pink);font-weight:600}
.lang{position:absolute;left:893px;top:31px;font-size:16px;color:#333}
.header-cta{position:absolute;left:977px;top:23px;padding:10px 14px}

/* hero */
.hero{position:absolute;left:0;top:78px;width:1200px;height:631px;background:linear-gradient(90deg,#ebebeb,#dcdcdc)}
.hero h1{position:absolute;left:111px;top:88px;width:600px;font-weight:400;font-size:58px;line-height:80px}
.hero h1 strong{color:var(--pink);font-weight:600}
.hero p{position:absolute;left:111px;top:326px;width:540px;font-size:18px;line-height:31px;color:var(--text)}
.hero .actions{position:absolute;left:111px;top:417px;display:flex;gap:14px}
.hero-photo{position:absolute;left:640px;top:0;width:560px;height:631px;background:linear-gradient(160deg,#e2e2e2,#c9ccd2 55%,#b9c5d6)}

/* services */
.section-title{position:absolute;width:1200px;text-align:center;font-weight:400;font-size:40px}
.section-title strong{color:var(--pink);font-weight:600}
.services{position:absolute;left:0;top:870px;width:1200px;display:flex;justify-content:center;gap:80px}
.service{width:230px;text-align:center}
.service .ring{width:116px;height:116px;margin:17px auto 0;border-radius:50%;border:10px solid #3a3a3a;display:flex;align-items:center;justify-content:center;box-shadow:4px 6px 10px rgba(0,0,0,.15)}
.service.featured .ring{border-color:var(--pink)}
.service h3{margin-top:36px;font-size:24px;font-weight:500}
.service.featured h3{color:var(--pink)}
.service p{margin-top:12px;font-size:14px;line-height:24px;color:var(--text)}

/* payrolling */
.payroll-photo{position:absolute;left:111px;top:1243px;width:447px;height:368px;border-radius:4px;background:linear-gradient(135deg,#4a5870,#2a3244 60%,#1d2230)}
.payroll-copy{position:absolute;left:643px;top:1232px;width:450px}
.payroll-copy h2{font-weight:400;font-size:42px}
.payroll-copy h2 strong{color:var(--pink);font-weight:600}
.payroll-copy .lead{margin-top:6px;font-size:13px;line-height:25px;color:var(--text)}
.checks{list-style:none;margin-top:18px}
.checks li{display:flex;gap:18px;font-size:13px;line-height:25px;color:var(--text);margin-bottom:20px}
.checks li b{color:var(--black);font-weight:600}
.checks svg{flex:none;margin-top:2px}
.payroll-copy .btn{margin-left:4px;margin-top:4px}

/* tools */
.tools{position:absolute;left:0;top:1718px;width:1200px;height:572px;background:var(--light)}
.tools .section-title{top:35px}
.tabs{position:absolute;left:274px;top:114px;width:642px;display:flex;border-bottom:3px solid #d9d9d9;font-size:16px}
.tab{padding:0 2px 10px;color:#444;width:50%;text-align:center}
.tab.active{color:var(--pink);border-bottom:3px solid var(--pink);margin-bottom:-3px}
.tools h3{position:absolute;left:110px;top:230px;font-size:22px;font-weight:500}
.tools .checks{position:absolute;left:110px;top:282px;margin:0}
.tools .checks li{margin-bottom:27px;font-size:13px}
.dashboard{position:absolute;left:632px;top:204px;width:476px;height:288px;border-radius:10px;background:linear-gradient(180deg,#f6f7fb,#dfe3ee)}

/* testimonials */
.clients-title{top:2375px}
.quote-mark{position:absolute;left:578px;top:2470px}
.testimonial{position:absolute;width:450px}
.avatar{width:76px;height:76px;border-radius:50%;background:linear-gradient(135deg,#c8c0b8,#8a7a6e)}
.person{display:flex;align-items:center;gap:20px}
.person .name{font-size:22px}
.person .role{font-size:17px;color:#444;margin-top:6px}
.testimonial p{margin-top:52px;font-size:16px;line-height:28px;color:var(--text)}
.arrow{position:absolute;top:2607px;width:21px;height:21px;border-radius:50%;display:flex;align-items:center;justify-content:center}

/* about */
.about{position:absolute;left:111px;top:2790px;width:430px}
.about h2{font-weight:400;font-size:42px}
.about h2 strong{color:var(--pink);font-weight:600}
.about p{margin:12px 4px 0;font-size:14px;line-height:29px;color:var(--text)}
.about h4{margin:22px 5px 0;color:var(--pink);font-weight:500;font-size:21px;text-decoration:underline}
.about .mission{font-style:italic;margin-top:8px}
.about .btn{margin:22px 4px 0}
.about-photo{position:absolute;left:642px;top:2800px;width:447px;height:368px;border-radius:4px;background:linear-gradient(135deg,#d8d4cc,#b8b2a8 50%,#8c8a84)}

/* footer */
.site-footer{position:absolute;left:0;top:3255px;width:1200px;height:369px;background:var(--footer);color:#fff}
.footer-brand{position:absolute;left:111px;top:80px;font-size:30px;font-weight:700;display:flex;align-items:center;gap:10px}
.footer-about{position:absolute;left:111px;top:150px;width:270px;font-size:13px;line-height:24px;font-weight:500}
.socials{position:absolute;left:114px;top:265px;display:flex;gap:5px}
.socials span{width:28px;height:28px;border-radius:50%;background:#fff;display:block}
.socials span:first-child{background:var(--pink)}
.footer-col{position:absolute;top:80px}
.footer-col h5{font-size:20px;font-weight:600;color:#e8e8e8;margin-bottom:10px}
.footer-col li{list-style:none;font-size:16px;line-height:30px}
.contact-item{display:flex;align-items:center;gap:14px;font-size:16px;margin-bottom:29px}
.copyright{position:absolute;left:111px;top:340px;width:984px;border-top:1px solid #777;padding-top:10px;text-align:center;font-size:14px}
</style>
</head>
<body>

<header class="site-header">
  <div class="brand"><span class="brand-mark"></span>BRISK The Answer</div>
  <nav class="main-nav">
    <span class="active">Home</span><span>Consultant</span><span>Business</span><span>Agency</span><span>About</span><span>Blog</span>
  </nav>
  <div class="lang">Eng &#8964;</div>
  <a class="btn header-cta">Contact US</a>
</header>

<section class="hero">
  <h1><strong>Your Payroll Partner,</strong><br>Backed by BRISK The Horizon</h1>
  <p>With the expertise of the BRISK group, we provide secure and compliant payroll solutions tailored to your needs.</p>
  <div class="actions"><a class="btn">Discover Our Services</a><a class="btn dark">Get in Touch</a></div>
  <div class="hero-photo" role="img" aria-label="Smiling woman holding a laptop with magenta accent shapes"></div>
</section>

<h2 class="section-title" style="top:785px">Our <strong>Services</strong></h2>
<div class="services">
  <div class="service">
    <div class="ring"><svg width="40" height="40" viewBox="0 0 40 40"><rect x="12" y="4" width="22" height="26" rx="2" fill="var(--pink)"/><circle cx="12" cy="22" r="6" fill="var(--pink)"/><rect x="4" y="29" width="16" height="8" rx="3" fill="var(--pink)"/></svg></div>
    <h3>Payrolling</h3>
    <p>Lorem ipsum dolor sit amet, consectetur adipiscing elit, sed do eiusmod tempor incididunt</p>
  </div>
  <div class="service featured">
    <div class="ring"><svg width="42" height="42" viewBox="0 0 42 42"><rect x="6" y="6" width="26" height="22" rx="2" fill="none" stroke="#3a3a3a" stroke-width="3"/><circle cx="27" cy="27" r="7" fill="none" stroke="var(--pink)" stroke-width="3"/><line x1="32" y1="32" x2="38" y2="38" stroke="var(--pink)" stroke-width="3"/></svg></div>
    <h3>Sourcing</h3>
    <p>Lorem ipsum dolor sit amet, consectetur adipiscing elit, sed do eiusmod tempor incididunt</p>
  </div>
  <div class="service">
    <div class="ring"><svg width="42" height="42" viewBox="0 0 42 42" fill="none" stroke="var(--pink)" stroke-width="2.5"><rect x="4" y="6" width="10" height="14"/><rect x="28" y="6" width="10" height="14"/><circle cx="21" cy="26" r="4"/><path d="M13 38c0-5 4-7 8-7s8 2 8 7"/><path d="M14 13h14"/></svg></div>
    <h3>Payroll Outsourcing</h3>
    <p>Lorem ipsum dolor sit amet, consectetur adipiscing elit, sed do eiusmod tempor incididunt</p>
  </div>
</div>

<div class="payroll-photo" role="img" aria-label="Hand touching a tablet with payroll icons in hexagons"></div>
<div class="payroll-copy">
  <h2>What is <strong>Payrolling?</strong></h2>
  <p class="lead">Payrolling is a flexible employment solution where a specialized company like BRISK The Answer becomes the legal employer of your staff.</p>
  <ul class="checks">
    <li><svg width="32" height="20" viewBox="0 0 32 20"><path d="M2 10l7 7L24 2" stroke="var(--pink)" stroke-width="3" fill="none"/><path d="M14 15l2 2 13-14" stroke="var(--pink)" stroke-width="2" fill="none"/></svg><span>We handle all <b>administrative tasks</b> employment contracts, payroll, social security, insurances, and tax compliance.</span></li>
    <li><svg width="32" height="20" viewBox="0 0 32 20"><path d="M2 10l7 7L24 2" stroke="var(--pink)" stroke-width="3" fill="none"/><path d="M14 15l2 2 13-14" stroke="var(--pink)" stroke-width="2" fill="none"/></svg><span>You retain full control over the <b>day-to-day management</b> of your employees (tasks, schedules, performance).</span></li>
    <li><svg width="32" height="20" viewBox="0 0 32 20"><path d="M2 10l7 7L24 2" stroke="var(--pink)" stroke-width="3" fill="none"/><path d="M14 15l2 2 13-14" stroke="var(--pink)" stroke-width="2" fill="none"/></svg><span>Your business gains flexibility, reduces risk, and saves time.</span></li>
  </ul>
  <a class="btn">Read More</a>
</div>

<section class="tools">
  <h2 class="section-title">High-Performance and <strong>Secure Digital Tools</strong></h2>
  <div class="tabs"><div class="tab active">Consultant space | Managing your activities</div><div class="tab">Business Space | Service Management</div></div>
  <h3>Consultant Space Managing Your Activities</h3>
  <ul class="checks">
    <li><svg width="32" height="20" viewBox="0 0 32 20"><path d="M2 10l7 7L24 2" stroke="var(--pink)" stroke-width="3" fill="none"/><path d="M14 15l2 2 13-14" stroke="var(--pink)" stroke-width="2" fill="none"/></svg><span>Luis aute irure dolor in reprehenderit in voluptate velit</span></li>
    <li><svg width="32" height="20" viewBox="0 0 32 20"><path d="M2 10l7 7L24 2" stroke="var(--pink)" stroke-width="3" fill="none"/><path d="M14 15l2 2 13-14" stroke="var(--pink)" stroke-width="2" fill="none"/></svg><span>Excepteur sint occaecat cupidatat non proident</span></li>
    <li><svg width="32" height="20" viewBox="0 0 32 20"><path d="M2 10l7 7L24 2" stroke="var(--pink)" stroke-width="3" fill="none"/><path d="M14 15l2 2 13-14" stroke="var(--pink)" stroke-width="2" fill="none"/></svg><span>Sed ut perspiciatis unde omnis iste natus error sit</span></li>
    <li><svg width="32" height="20" viewBox="0 0 32 20"><path d="M2 10l7 7L24 2" stroke="var(--pink)" stroke-width="3" fill="none"/><path d="M14 15l2 2 13-14" stroke="var(--pink)" stroke-width="2" fill="none"/></svg><span>Nemo enim ipsam voluptatem quia voluptas</span></li>
    <li><svg width="32" height="20" viewBox="0 0 32 20"><path d="M2 10l7 7L24 2" stroke="var(--pink)" stroke-width="3" fill="none"/><path d="M14 15l2 2 13-14" stroke="var(--pink)" stroke-width="2" fill="none"/></svg><span>Voluptate velit esse quam nihil molestiae consequatur</span></li>
  </ul>
  <div class="dashboard" role="img" aria-label="Laptop showing an analytics dashboard with charts"></div>
</section>

<h2 class="section-title clients-title">What Our <strong>Clients Say</strong></h2>
<svg class="quote-mark" width="36" height="32" viewBox="0 0 36 32"><path d="M16 2C6 6 2 13 2 20a6 6 0 1 0 8-6c1-4 4-8 8-10zM34 2c-10 4-14 11-14 18a6 6 0 1 0 8-6c1-4 4-8 8-10z" fill="var(--pink)"/></svg>
<div class="arrow" style="left:36px;background:var(--pink)"><svg width="11" height="11" viewBox="0 0 11 11"><path d="M10 5.5H2M5 2L1.5 5.5 5 9" stroke="#fff" stroke-width="2" fill="none"/></svg></div>
<div class="arrow" style="left:1138px;background:#a8a8a8"><svg width="11" height="11" viewBox="0 0 11 11"><path d="M1 5.5h8M6 2l3.5 3.5L6 9" stroke="#fff" stroke-width="2" fill="none"/></svg></div>
<div class="testimonial" style="left:110px;top:2508px">
  <div class="person"><div class="avatar" role="img" aria-label="Client portrait"></div><div><div class="name">Julien R.</div><div class="role">Project Director</div></div></div>
  <p>“BRISK The Answer made our hiring process so much easier. We save hours every week thanks to their payroll management.”</p>
</div>
<div class="testimonial" style="left:645px;top:2504px">
  <div class="person"><div class="avatar" role="img" aria-label="Client portrait"></div><div><div class="name">Claire D.</div><div class="role">Entrepreneure</div></div></div>
  <p>“Professionnels, transparents et rapides. Nous pouvons nous concentrer sur nos projets en toute sérénité, la paie et la conformité sont entre de bonnes mains”.</p>
</div>

<section class="about">
  <h2>Who We <strong>Are</strong></h2>
  <p>BRISK The Answer is a Swiss company specialized in payrolling services. As part of the BRISK The Horizon Group, we combine inntovation, expertise, and reliability to help businesses simplify their employment processes.</p>
  <h4>Our mission</h4>
  <p class="mission">We manage the administrative complexity of employment so you can focus on your people and your growth.</p>
  <a class="btn">Read More</a>
</section>
<div class="about-photo" role="img" aria-label="Team meeting around a desk with charts and a computer"></div>

<footer class="site-footer">
  <div class="footer-brand"><span class="brand-mark"></span>BRISK The Answer</div>
  <p class="footer-about">Neque porro quisquam est, qui dolorem ipsum quia dolor sit amet, consectetur, adipisci velit</p>
  <div class="socials" aria-label="Social links"><span></span><span></span><span></span><span></span><span></span></div>
  <div class="footer-col" style="left:449px"><h5>Quick Links</h5><ul><li>Home</li><li>Consultant</li><li>Business</li><li>Agency</li><li>About</li><li>Blog</li></ul></div>
  <div class="footer-col" style="left:620px"><h5>Other Links</h5><ul><li>Privacy Policy</li><li>Terms &amp; Condotions</li><li>Disclaimer</li><li>FAQ's</li><li>Support</li><li>Help</li></ul></div>
  <div class="footer-col" style="left:849px"><h5>Contact Us</h5>
    <div class="contact-item"><svg width="20" height="20" viewBox="0 0 20 20"><path d="M10 1a7 7 0 0 0-7 7c0 5 7 11 7 11s7-6 7-11a7 7 0 0 0-7-7z" fill="#fff"/><circle cx="10" cy="8" r="3" fill="var(--footer)"/></svg>Lorem Ipsum,USA - 437916</div>
    <div class="contact-item"><svg width="20" height="20" viewBox="0 0 20 20"><circle cx="10" cy="10" r="10" fill="#fff"/><path d="M6 5l2 0 1 3-1.5 1a7 7 0 0 0 3.5 3.5L12 11l3 1v2c-5 1-10-4-9-9z" fill="var(--footer)"/></svg>+1 555 010 2040</div>
    <div class="contact-item"><svg width="20" height="20" viewBox="0 0 20 20"><circle cx="10" cy="10" r="10" fill="#fff"/><rect x="5" y="6.5" width="10" height="7" fill="none" stroke="var(--footer)" stroke-width="1.5"/><path d="M5 7l5 4 5-4" stroke="var(--footer)" stroke-width="1.5" fill="none"/></svg>info@brisktheanswer.com</div>
  </div>
  <div class="copyright">© 2025 BRISK The Answer .All rights reserved</div>
</footer>

</body>
</html>
```